Sun Meadow Home Care Business Card

We are a home care company customizing in personal care services. Our personal care service is different because our mission is to provide the most effective care while enhancing quality of life. We strive to make everyday our client's best day. I would like a very classic and/or retro feel. I don't like clip art.

Target Market(s)

doctor's offices; potential clients

Industry/Entity Type

Business

Contact Information for Business Card

tlangford@sunmeadowhc.example(919) 480-15904000 Blue Ridge Road, Suite 101Raleigh, NC 27612www.BeWellHC.com

Requirements
Must have
• classic and/or retro feel. Very caring.
Should not have
• Clip art

```html
<!DOCTYPE html>
<html lang="en">
<head>
<meta charset="utf-8">
<title>Sun Meadow Home Care – Business Card</title>
<link rel="stylesheet" href="https://fonts.googleapis.com/css2?family=Bebas+Neue&display=swap">
<style>
  :root {
    --backdrop: #2f2e2e;
    --frame-blue: #3a97c9;
    --card-paper: #ececec;
    --ink: #2a2a2a;
    --brand-blue: #2a9ad3;
    --ornament-tone: #b9b9b9;
  }
  html, body {
    margin: 0;
    padding: 0;
    width: 1200px;
    height: 720px;
    overflow: hidden;
    background: var(--backdrop);
  }
  .card {
    position: relative;
    width: 1200px;
    height: 720px;
    font-family: "Bebas Neue", "Oswald", sans-serif;
    color: var(--ink);
  }
  .card-frame {
    position: absolute;
    inset: 0;
  }
  .brand-name {
    position: absolute;
    left: 0;
    width: 1200px;
    top: 146px;
    margin: 0;
    text-align: center;
    font-weight: 400;
    font-size: 62px;
    line-height: 62px;
    letter-spacing: 2px;
    color: var(--brand-blue);
  }
  .contact-line {
    position: absolute;
    left: 0;
    width: 1200px;
    margin: 0;
    text-align: center;
    font-size: 33px;
    line-height: 36px;
    letter-spacing: 0.5px;
  }
  .contact-address { top: 324px; }
  .contact-phone   { top: 406px; }
  .contact-email   { top: 493px; }
  .contact-web     { top: 580px; }
  .divider {
    position: absolute;
    left: 406px;
    width: 392px;
    height: 20px;
  }
  .divider-1 { top: 372px; }
  .divider-2 { top: 456px; }
  .divider-3 { top: 544px; }
</style>
</head>
<body>
<div class="card">
  <svg class="card-frame" width="1200" height="720" viewBox="0 0 1200 720" aria-hidden="true">
    <rect x="68" y="68" width="1063" height="583" fill="none" stroke="var(--frame-blue)" stroke-width="5"/>
    <rect x="66" y="66" width="22" height="22" fill="var(--frame-blue)"/>
    <rect x="1111" y="66" width="22" height="22" fill="var(--frame-blue)"/>
    <rect x="66" y="631" width="22" height="22" fill="var(--frame-blue)"/>
    <rect x="1111" y="631" width="22" height="22" fill="var(--frame-blue)"/>
    <path fill="var(--card-paper)"
      d="M101 81 H1098 V95 H1113 V626 H1098 V640 H101 V626 H87 V95 H101 Z"/>
  </svg>

  <h1 class="brand-name">Sun Meadow<br>Home Care, Inc.</h1>

  <p class="contact-line contact-address">Harlow Creek Road, Suite 101 Raleigh, NC 27699</p>

  <svg class="divider divider-1" viewBox="0 0 392 20">
    <line x1="0" y1="10" x2="392" y2="10" stroke="var(--ink)" stroke-width="1.5"/>
    <rect x="180" y="4" width="32" height="12" fill="var(--ornament-tone)" role="img" aria-label="Small knot ornament at the centre of the divider"/>
  </svg>

  <p class="contact-line contact-phone">(919) 555-0143</p>

  <svg class="divider divider-2" viewBox="0 0 392 20">
    <line x1="0" y1="10" x2="392" y2="10" stroke="var(--ink)" stroke-width="1.5"/>
    <rect x="180" y="4" width="32" height="12" fill="var(--ornament-tone)" role="img" aria-label="Small knot ornament at the centre of the divider"/>
  </svg>

  <p class="contact-line contact-email">tlangford@sunmeadowhc.example</p>

  <svg class="divider divider-3" viewBox="0 0 392 20">
    <line x1="0" y1="10" x2="392" y2="10" stroke="var(--ink)" stroke-width="1.5"/>
    <rect x="180" y="4" width="32" height="12" fill="var(--ornament-tone)" role="img" aria-label="Small knot ornament at the centre of the divider"/>
  </svg>

  <p class="contact-line contact-web">www.SunMeadowHC.example</p>
</div>
</body>
</html>
```